Coastline Premier Retreats Business Card Design

Design a business card for Coastline Premier Retreats. Look at the website for colors and reference. Card should have logo, name, title, office number, mobile number, email, URL and a tagline like, "Luxury Hotel & Resort Email Marketing" (This might change).

https://www.coastlinepremierretreats.example

The rest I will leave up to your imagination.

Contact Information for Business Card

Logo, name, title, office number, mobile number, email, URL and a tagline like, "Luxury Hotel & Resort Email Marketing" (This might change).

```html
<!DOCTYPE html>
<html lang="en">
<head>
<meta charset="utf-8">
<title>Coastline Premier Retreats – Business Card</title>
<link href="https://fonts.googleapis.com/css2?family=Arimo:wght@400;700&display=swap" rel="stylesheet">
<style>
  :root {
    --stage: #1d1d1d;
    --paper: #f4f4f4;
    --card-dark: #161616;
    --accent: #e8711c;
    --ink: #2f2f2f;
    --ink-soft: #3c3c3c;
    --emboss: #2e2e2e;
  }
  * { margin: 0; padding: 0; box-sizing: border-box; }
  html, body { width: 1200px; height: 1059px; overflow: hidden; }
  body {
    background: var(--stage);
    font-family: "Arimo", Arial, sans-serif;
    position: relative;
  }
  .card { position: absolute; }
  .card-front {
    left: 256px; top: 89px; width: 688px; height: 391px;
    background: var(--paper);
  }
  .card-back {
    left: 253px; top: 546px; width: 695px; height: 395px;
    background: var(--card-dark);
    display: flex; align-items: center; justify-content: center;
  }
  .frame-line { position: absolute; background: var(--accent); }
  .frame-top { left: 23px; top: 22px; width: 643px; height: 2px; }
  .frame-left { left: 23px; top: 22px; width: 2px; height: 337px; }
  .frame-right { left: 664px; top: 22px; width: 2px; height: 337px; }
  .frame-bottom-left { left: 23px; top: 357px; width: 155px; height: 2px; }
  .frame-bottom-right { left: 511px; top: 357px; width: 155px; height: 2px; }
  .tagline {
    position: absolute; left: 178px; width: 333px; top: 347px;
    text-align: center; font-size: 17px; color: var(--ink); line-height: 20px;
  }
  .brand {
    position: absolute; left: 59px; top: 178px; width: 258px;
    display: flex; align-items: center; gap: 10px;
  }
  .brand-mark { width: 14px; height: 14px; background: var(--accent); flex: none; }
  .brand-name { font-size: 19px; font-weight: 700; color: var(--ink); letter-spacing: 0.2px; }
  .divider {
    position: absolute; left: 349px; top: 100px; width: 1px; height: 190px;
    background: var(--accent);
  }
  .details { position: absolute; left: 379px; top: 95px; color: var(--ink-soft); }
  .person-name {
    font-size: 29px; font-weight: 700; color: var(--accent); line-height: 32px; letter-spacing: 0.3px;
  }
  .person-title { font-size: 16px; line-height: 18px; margin-top: 0; }
  .address { font-size: 16px; line-height: 20px; margin-top: 14px; }
  .contact-list { list-style: none; margin-top: 10px; }
  .contact-item {
    display: flex; align-items: center; gap: 6px;
    font-size: 14.5px; line-height: 21.5px;
  }
  .contact-icon { width: 12px; height: 12px; flex: none; fill: var(--accent); }
  .back-brand {
    font-size: 38px; font-weight: 700; color: var(--emboss);
    letter-spacing: 0.5px;
  }
</style>
</head>
<body>
  <section class="card card-front" aria-label="Business card front">
    <div class="frame-line frame-top"></div>
    <div class="frame-line frame-left"></div>
    <div class="frame-line frame-right"></div>
    <div class="frame-line frame-bottom-left"></div>
    <div class="frame-line frame-bottom-right"></div>

    <div class="brand">
      <span class="brand-mark"></span>
      <span class="brand-name">Coastline Premier Retreats</span>
    </div>

    <div class="divider"></div>

    <div class="details">
      <h1 class="person-name">DANIEL HART</h1>
      <p class="person-title">CEO/Founder</p>
      <p class="address">PO Box 48, 210 Harbor Rd<br>Seaview Bay, CA 90210</p>
      <ul class="contact-list">
        <li class="contact-item">
          <svg class="contact-icon" viewBox="0 0 12 12"><path d="M3 0h6a1 1 0 0 1 1 1v10a1 1 0 0 1-1 1H3a1 1 0 0 1-1-1V1a1 1 0 0 1 1-1zm.6 1.4v8h4.8v-8zM6 9.9a.6.6 0 1 0 0 1.2.6.6 0 0 0 0-1.2z"/></svg>
          555.014.2200
        </li>
        <li class="contact-item">
          <svg class="contact-icon" viewBox="0 0 12 12"><path d="M0 4c0-1.5 2.7-2.6 6-2.6S12 2.5 12 4v1H9V3.8H3V5H0zM3 6h6l2 2.2V11H1V8.2zm3 1.2a1.3 1.3 0 1 0 0 2.6 1.3 1.3 0 0 0 0-2.6z"/></svg>
          +34 600 412 077
        </li>
        <li class="contact-item">
          <svg class="contact-icon" viewBox="0 0 12 12"><path d="M0 5l6-4 6 4v6H0zm1.3.6L6 8.6l4.7-3L6 2.6z"/></svg>
          info@coastlinepremierretreats.example
        </li>
        <li class="contact-item">
          <svg class="contact-icon" viewBox="0 0 12 12"><path d="M6 0a6 6 0 1 1 0 12A6 6 0 0 1 6 0zm0 1.3a4.7 4.7 0 0 0-3.9 7.3L4 7V5.3l2-1.5V1.3zm1.2.2v2l2 1.4V7l-1.6 2.5A4.7 4.7 0 0 0 7.2 1.5z"/></svg>
          www.coastlinepremierretreats.example
        </li>
      </ul>
    </div>

    <p class="tagline">Luxury Hotel &amp; Resort Email Marketing</p>
  </section>

  <section class="card card-back" aria-label="Business card back">
    <span class="back-brand">Coastline Premier Retreats</span>
  </section>
</body>
</html>
```